Homemaking training schools needs a Business Card design

Designer, Hello!

No special requirements, good-looking enough.
--------------------------------------------------------------------------

Name: Marcus Dole
Chairman
Tel: 0574-71948263
Mobile: 13857420916
Email: kelvora@mailnest.example
Web: www.prt2019.example
Add: No.258, LanpingJie, BeiyuanQu, Ningbo, Zhejiang

LOGO
Ningbo PRT Homemaking Training School

Target Market(s)

pregnant women, mothers, infants, the elderly and families, including cleaning, cooking, nursing training.

Industry/Entity Type

Business

Contact Information for Business Card

Name: Marcus Dole
Chairman
Tel: 0574-71948263
Mobile: 13857420916
Email: kelvora@mailnest.example
Web: www.prt2019.example

LOGO

Font styles to use
Serif
Sans Serif
Decorative

Requirements
Nice to have
• Feels: clean, specifications, safety, comfort, warmth and happiness.

```html
<!DOCTYPE html>
<html lang="en">
<head>
<meta charset="UTF-8">
<title>PeiRongTai Training &amp; Services – Business Card</title>
<link rel="stylesheet" href="https://fonts.googleapis.com/css2?family=Comfortaa:wght@400;700&family=Damion&family=Josefin+Sans:wght@600&display=swap">
<style>
  :root {
    --card-green: #73c8a9;
    --brand-blue: #1b75bc;
    --ink-grey: #3d4a45;
    --rust: #c9553a;
    --white: #ffffff;
  }
  html, body {
    margin: 0;
    padding: 0;
    width: 1200px;
    height: 704px;
    overflow: hidden;
    background: var(--card-green);
  }
  .card {
    position: relative;
    width: 1200px;
    height: 704px;
    background: var(--card-green);
    overflow: hidden;
  }
  .ornament {
    position: absolute;
    left: 559px;
    width: 82px;
    height: 30px;
    background: var(--white);
    opacity: 0.85;
    border-radius: 3px;
  }
  .ornament--top { top: 23px; }
  .ornament--bottom { top: 642px; }
  .brand-name {
    position: absolute;
    left: 0;
    top: 268px;
    width: 1200px;
    margin: 0;
    text-align: center;
    font-family: "Comfortaa", sans-serif;
    font-weight: 700;
    font-size: 128px;
    line-height: 1;
    letter-spacing: -2px;
    color: var(--brand-blue);
  }
  .tagline-row {
    position: absolute;
    left: 143px;
    top: 412px;
    width: 917px;
    display: flex;
    align-items: center;
    gap: 18px;
  }
  .tagline-rule {
    flex: 1;
    height: 3px;
    background: var(--ink-grey);
  }
  .tagline {
    margin: 0;
    font-family: "Comfortaa", sans-serif;
    font-weight: 400;
    font-size: 46px;
    line-height: 1;
    color: var(--ink-grey);
    white-space: nowrap;
  }
  .person {
    position: absolute;
    left: 400px;
    top: 508px;
    width: 400px;
    text-align: center;
  }
  .person-name {
    margin: 0;
    font-family: "Damion", cursive;
    font-weight: 400;
    font-size: 58px;
    line-height: 1;
    color: var(--rust);
  }
  .person-title {
    margin: 14px 0 0;
    font-family: "Josefin Sans", sans-serif;
    font-weight: 600;
    font-size: 16px;
    letter-spacing: 2px;
    color: var(--rust);
  }
  .contact {
    position: absolute;
    left: 810px;
    top: 580px;
    margin: 0;
    padding: 0;
    list-style: none;
    font-family: "Josefin Sans", sans-serif;
    font-weight: 600;
    font-size: 16px;
    line-height: 20px;
    letter-spacing: 2px;
    text-transform: uppercase;
    color: var(--rust);
    white-space: nowrap;
  }
  .contact-item { display: flex; }
  .contact-item--address { margin-top: 20px; }
  .contact-key { width: 34px; flex: none; }
</style>
</head>
<body>
  <main class="card">
    <div class="ornament ornament--top" role="img" aria-label="Small white decorative ornament"></div>

    <h1 class="brand-name">PeiRongTai</h1>
    <div class="tagline-row">
      <span class="tagline-rule"></span>
      <p class="tagline">Training &amp; Services</p>
      <span class="tagline-rule"></span>
    </div>

    <section class="person">
      <h2 class="person-name">Marcus Dole</h2>
      <p class="person-title">CHAIRMAN</p>
    </section>

    <ul class="contact">
      <li class="contact-item"><span class="contact-key">T.</span><span>&nbsp;0574-71948263</span></li>
      <li class="contact-item"><span class="contact-key">E.</span><span>kelvora@mailnest.example</span></li>
      <li class="contact-item"><span class="contact-key">W.</span><span>www.prt2019.example</span></li>
      <li class="contact-item contact-item--address"><span class="contact-key">A.</span><span>No.258, LanpingJie, BeiyuanQu,<br>Ningbo, Zhejian</span></li>
    </ul>

    <div class="ornament ornament--bottom" role="img" aria-label="Small white decorative ornament"></div>
  </main>
</body>
</html>
```